Bright bears day nursery qrp limited

we would like create a website that can be updated by us easily as we have regular changes to what we provide and need. we would like something that is classy but also appealing from a child's aspect. we would be looking to add our own logo and our kinderwatch logo both attached, if you guys can create it and we will work with the preferred choice to add all the text.
We would like the links to family pathways, kinderwatch report and our chatterbook feed on the front page

we are looking for a website for our childcare business we have 2 nurseries that we would like one website.
showing our opening hours, price list, policies etc as well as photos, description of our day, staff photos and their training accreditation's.

Target Market(s)

Families

Industry/Entity Type

Childcare

Number of Pages Required

5+ page

Font styles to use
Serif

Colors

Designer to choose colors to be used in the design.

Requirements
Must have
• links to social media and other websites, photographs, links to download registration forms etc, parents able to leave reviews. google maps link, job opportunities
Nice to have
• facilities to take payments

```html
<!DOCTYPE html>
<html lang="en">
<head>
<meta charset="utf-8">
<title>Bright Bears Day Nursery</title>
<link href="https://fonts.googleapis.com/css2?family=Lato:wght@400;700;900&family=Montserrat:wght@700&display=swap" rel="stylesheet">
<style>
:root{
  --green:#5bb04b;
  --pink:#d22a80;
  --navy:#2b4a87;
  --slate:#6c7699;
  --footer:#343d68;
  --ink:#2a2a2a;
  --muted:#8a8a8a;
  --line:#e3e3e3;
  --soft:#f7f7f7;
  --white:#ffffff;
}
*{margin:0;padding:0;box-sizing:border-box}
html,body{width:1200px;height:2659px;overflow:hidden;background:var(--white);font-family:"Lato",sans-serif;color:var(--ink)}
.page{position:relative;width:1200px;height:2659px}
.abs{position:absolute}

/* header */
.header{top:0;left:0;width:1200px;height:145px;background:var(--white)}
.brand{left:99px;top:34px;display:flex;align-items:center;gap:12px}
.brand-mark{width:22px;height:22px;background:var(--pink);border-radius:4px}
.brand-name{font-weight:900;font-size:22px;line-height:1.1;color:var(--navy);width:150px;text-transform:uppercase}
.nav{right:98px;top:64px;display:flex}
.nav a{font-size:14px;color:#444;text-decoration:none;letter-spacing:.3px;margin-left:62px;position:relative}
.nav a.active::after{content:"";position:absolute;left:0;right:0;bottom:-10px;height:2px;background:#444}

/* hero */
.hero{top:145px;left:0;width:1200px;height:599px;background:
  linear-gradient(180deg,rgba(40,45,55,.25) 0%,rgba(40,45,55,.35) 50%,rgba(40,45,55,.1) 100%),
  linear-gradient(90deg,#9aa4ae 0%,#b3aca2 30%,#c39a6a 55%,#8f7a68 75%,#6f8fb6 100%)}
.hero-title{top:320px;left:0;width:1200px;text-align:center;font-weight:900;font-size:60px;color:var(--white);letter-spacing:.5px;text-shadow:0 2px 8px rgba(0,0,0,.35)}
.hero-sub{top:404px;left:190px;width:820px;text-align:center;font-size:14px;line-height:20px;color:var(--white);text-shadow:0 1px 4px rgba(0,0,0,.45)}
.hero-arrow{top:388px;width:44px;height:44px;border-radius:50%;background:rgba(255,255,255,.35)}
.hero-arrow svg{display:block}

/* day */
.day{top:744px;left:0;width:1200px;height:373px;background:var(--green)}
.day-title{left:98px;top:808px;font-family:"Montserrat",sans-serif;font-weight:700;font-size:29px;color:var(--white)}
.day-text{left:99px;top:866px;width:548px;font-size:12px;line-height:24px;color:var(--white)}
.btn-light{left:99px;top:1004px;width:178px;height:38px;background:var(--white);color:var(--green);font-size:17px;display:flex;align-items:center;justify-content:center}
.day-photo{left:707px;top:808px;width:394px;height:250px;border:5px solid var(--white);border-radius:6px;background:
  linear-gradient(180deg,#e7e2dc 0%,#d9c8b2 35%,#b98a5e 36%,#c99b6e 55%,#d9e03a 70%,#c6cf2e 100%)}

/* staff */
.section-title{font-weight:700;font-size:29px;color:var(--ink)}
.staff-title{left:99px;top:1168px}
.staff-rule{left:99px;top:1237px;width:1002px;height:1px;background:var(--line)}
.circ-btn{width:36px;height:36px;border-radius:50%;background:#e6e6e6;top:1174px}
.staff-card{top:1276px;width:316px}
.staff-photo{height:183px;width:316px}
.staff-name{margin-top:26px;font-size:20px;font-weight:700;color:var(--ink);letter-spacing:.2px}
.staff-text{margin-top:14px;font-size:14.5px;line-height:21px;color:var(--muted);width:250px}
.staff-btn{margin-top:23px;width:142px;height:40px;display:flex;align-items:center;justify-content:center;color:var(--white);font-size:15px}

/* info */
.info{top:1734px;left:0;width:1200px;height:476px;background:var(--soft)}
.info-title{top:1792px;font-size:20px;font-weight:700;display:flex;align-items:center;gap:8px}
.panel{top:1838px;height:301px;background:var(--white);border:1px solid #dcdcdc}
.panel-head{height:36px;display:flex;align-items:center;color:var(--white);font-size:15px}
.feed-photo{margin:8px 8px 0;height:95px;background:linear-gradient(90deg,#2c2b3a,#4a4356)}
.feed-likes{margin:12px 8px 0;font-size:15px;font-weight:700;color:#222}
.faces{margin:10px 8px 0;display:grid;grid-template-columns:repeat(5,1fr);gap:5px}
.faces span{height:46px;background:linear-gradient(135deg,#c9a48a,#7d6555)}
.price-table{width:100%;border-collapse:collapse;font-size:11.5px}
.price-table td{padding:6px 10px;border-bottom:1px solid var(--line);vertical-align:middle;line-height:15px}
.price-table td.val{color:var(--pink);width:82px}
.price-note{font-size:10px;text-align:center;color:#333;line-height:13px;padding-top:10px}
.hours-table{width:100%;border-collapse:collapse;font-size:11.5px;color:#444}
.hours-table td{height:36px;padding:0 14px;border-bottom:1px solid var(--line)}
.hours-table td+td{text-align:right;border-left:1px solid var(--line)}

/* accreditations */
.accred{top:2210px;left:0;width:1200px;height:241px;background:var(--slate)}
.seal{top:2272px;width:106px;height:106px;border-radius:50%}

/* footer */
.footer{top:2451px;left:0;width:1200px;height:208px;background:var(--footer)}
.foot-links{top:2482px;left:0;width:1200px;text-align:center;font-size:10.5px;color:var(--white)}
.socials{top:2528px;left:544px;display:flex;gap:12px}
.socials span{width:20px;height:20px;border-radius:4px;background:var(--white)}
.foot-rule{top:2574px;left:99px;width:1002px;height:1px;background:rgba(255,255,255,.15)}
.copyright{top:2611px;left:99px;font-size:12px;color:var(--white);letter-spacing:.3px}
.foot-badge{top:2586px;height:56px;background:var(--white);border-radius:2px}
.foot-code{top:2611px;left:1144px;font-size:12px;color:var(--white)}
</style>
</head>
<body>
<div class="page">

  <header class="header abs">
    <div class="brand abs">
      <span class="brand-mark"></span>
      <span class="brand-name">Bright Bears Day Nursery</span>
    </div>
    <nav class="nav abs">
      <a class="active">HOME</a><a>ABOUT US</a><a>OUR SERVICES</a><a>PRICE LIST</a><a>BLOG</a><a>CONTACT US</a>
    </nav>
  </header>

  <section class="hero abs" role="img" aria-label="Photo of a carer playing with young children in a bright playroom"></section>
  <h1 class="hero-title abs">BRIGHT BEARS DAY CARE NURSERY</h1>
  <p class="hero-sub abs">Quis autem vel eum iure reprehenderit qui in ea voluptate velit esse quam nihil molestiae consequatur, vel illum qui dolorem eum fugiat quo voluptas nulla pariatur.</p>
  <div class="hero-arrow abs" style="left:20px"><svg width="44" height="44"><path d="M26 14 L18 22 L26 30" fill="none" stroke="#fff" stroke-width="2"/></svg></div>
  <div class="hero-arrow abs" style="left:1128px"><svg width="44" height="44"><path d="M18 14 L26 22 L18 30" fill="none" stroke="#fff" stroke-width="2"/></svg></div>

  <section class="day abs"></section>
  <h2 class="day-title abs">DESCRIPTION OF OUR DAY</h2>
  <p class="day-text abs">Sed ut perspiciatis unde omnis iste natus error sit voluptatem accusantium doloremque laudantium, totam rem aperiam, eaque ipsa quae ab illo inventore veritatis et quasi architecto beatae vitae dicta sunt explicabo. Nemo enim ipsam voluptatem quia voluptas sit aspernatur aut odit aut fugit, sed quia consequuntur magni dolores eos qui ratione voluptatem sequi nesciunt.</p>
  <div class="btn-light abs">View more</div>
  <div class="day-photo abs" role="img" aria-label="Photo of toddlers playing at a low yellow table"></div>

  <h2 class="section-title staff-title abs">OUR STAFF</h2>
  <div class="circ-btn abs" style="left:1029px"><svg width="36" height="36"><path d="M20 13 L15 18 L20 23" fill="none" stroke="#555" stroke-width="1.6"/></svg></div>
  <div class="circ-btn abs" style="left:1065px"><svg width="36" height="36"><path d="M16 13 L21 18 L16 23" fill="none" stroke="#555" stroke-width="1.6"/></svg></div>
  <div class="staff-rule abs"></div>

  <article class="staff-card abs" style="left:99px">
    <div class="staff-photo" role="img" aria-label="Photo of a staff member playing with toddlers" style="background:linear-gradient(160deg,#f1e3dc 0%,#d9b39c 40%,#9c8ac2 70%,#c8d56a 100%)"></div>
    <h3 class="staff-name">NISI UT ALIQUID EX</h3>
    <p class="staff-text">Ut enim ad minima veniam nostrum exercitationem ullam corporis suscipit laboriosam, nisi ut aliquid..</p>
    <div class="staff-btn" style="background:var(--pink)">Read More &#8250;</div>
  </article>
  <article class="staff-card abs" style="left:441px">
    <div class="staff-photo" role="img" aria-label="Photo of a staff member helping a child with building blocks" style="background:linear-gradient(160deg,#dfe3c8 0%,#b7a58a 40%,#7e8a5c 75%,#5f6e45 100%)"></div>
    <h3 class="staff-name">MAGNI DOLORES EOS</h3>
    <p class="staff-text">Ut enim ad minima veniam nostrum exercitationem ullam corporis suscipit laboriosam, nisi ut aliquid..</p>
    <div class="staff-btn" style="background:var(--green)">Read More &#8250;</div>
  </article>
  <article class="staff-card abs" style="left:785px">
    <div class="staff-photo" role="img" aria-label="Photo of a staff member playing with a baby and ring toys" style="background:linear-gradient(160deg,#e8ddd2 0%,#c7a58a 40%,#6e7890 70%,#d6c24a 100%)"></div>
    <h3 class="staff-name">QUASI ARCHITECTO BEATAE</h3>
    <p class="staff-text">Ut enim ad minima veniam nostrum exercitationem ullam corporis suscipit laboriosam, nisi ut aliquid..</p>
    <div class="staff-btn" style="background:var(--navy)">Read More &#8250;</div>
  </article>

  <section class="info abs"></section>
  <h3 class="info-title abs" style="left:99px;color:var(--navy)"><span style="width:16px;height:16px;background:var(--navy);border-radius:2px;display:inline-block"></span>CHATTERBOOK FEED</h3>
  <h3 class="info-title abs" style="left:442px;color:var(--green)">PRICE LIST</h3>
  <h3 class="info-title abs" style="left:788px;color:var(--pink)">OPENING HOURS</h3>

  <div class="panel abs" style="left:99px;width:313px">
    <div class="panel-head" style="background:var(--navy);padding-left:12px">Find us on Chatterbook</div>
    <div class="feed-photo" role="img" aria-label="Cover photo of the nursery page"></div>
    <p class="feed-likes">85 people like information.</p>
    <div class="faces" role="img" aria-label="Thumbnails of page followers"><span></span><span></span><span></span><span></span><span></span><span></span><span></span><span></span><span></span><span></span></div>
  </div>

  <div class="panel abs" style="left:443px;width:314px">
    <div class="panel-head" style="background:var(--green)"><span style="margin-left:146px">Under 2's</span><span style="margin-left:30px">2-5's</span></div>
    <table class="price-table">
      <tr><td>Half day<br>8am-1pm or 1pm-6pm</td><td class="val">£26</td><td class="val">£25</td></tr>
      <tr><td>Full day<br>(7.30-6pm)</td><td class="val">£40</td><td class="val">£38</td></tr>
      <tr><td>Full time<br>Mon- Fri<br>7.30-6pm</td><td class="val">£168</td><td class="val">£161</td></tr>
      <tr><td>Full time funded children<br>3+ years old*<br>During term time</td><td class="val">xxxxxxxxxx</td><td class="val">£130</td></tr>
    </table>
    <p class="price-note">Fees include breakfast (full day/full time only)<br>A light snack each session, nappies and wipes.</p>
  </div>

  <div class="panel abs" style="left:789px;width:312px">
    <div class="panel-head" style="background:var(--pink);padding-left:12px">Hours</div>
    <table class="hours-table">
      <tr><td>Monday</td><td>8:00 AM - 9:00 PM</td></tr>
      <tr><td>Tuesday</td><td>8:00 AM - 9:00 PM</td></tr>
      <tr><td>Wednesday</td><td>8:00 AM - 9:00 PM</td></tr>
      <tr><td>Thursday</td><td>8:00 AM - 9:00 PM</td></tr>
      <tr><td>Friday</td><td>8:00 AM - 9:00 PM</td></tr>
      <tr><td>Saturday</td><td>9:00 AM - 6:00 PM</td></tr>
      <tr><td style="border-bottom:0">Sunday</td><td style="border-bottom:0">CLOSED</td></tr>
    </table>
  </div>

  <section class="accred abs"></section>
  <div class="seal abs" style="left:200px;background:#4a4a4a;border:3px solid #bdbdbd"></div>
  <div class="seal abs" style="left:434px;background:#8c8c95"></div>
  <div class="seal abs" style="left:659px;background:#5b5b5b;border:3px solid #cfcfcf;border-radius:18px"></div>
  <div class="seal abs" style="left:890px;background:#4f4f4f;border:3px solid #cfcfcf"></div>

  <footer class="footer abs"></footer>
  <p class="foot-links abs">Terms of Service &nbsp;|&nbsp; Policies &nbsp;|&nbsp; Contact</p>
  <div class="socials abs"><span></span><span></span><span></span><span></span></div>
  <div class="foot-rule abs"></div>
  <p class="copyright abs">2017 BRIGHT BEARS DAY CARE NURSERY © ALL RIGHTS RESERVED.</p>
  <div class="foot-badge abs" style="left:851px;width:101px"></div>
  <div class="foot-badge abs" style="left:967px;width:56px;background:#1f3b8c"></div>
  <div class="foot-badge abs" style="left:1038px;width:64px;background:#1f3b8c"></div>
  <p class="foot-code abs">C16</p>

</div>
</body>
</html>
```